Merrisol. Sunless Tanning Mousse Label

I'm looking for a label creation for a new brand of sunless tanning solutions. They are in 6.7oz bottles (template attached).

For the front of the bottle (see template) I would like an abstract multi coloured design taking up just over half the top of the bottle (approx 60%) and going around the design (this is similar to the design inspiration attached). I would this design to use the attached colour palette of pinks. It can be swirls, drips, squares, lines, whatever you think will look good.

The logo will then be over top of that abstract design in the upper 1/3, in the colour #3fe0d0

Under the abstract design the following text:

Amber Hush (Larger text)
Violet Base (2nd heading)
1 Hour Sunless Mousse (Sub text)
The No Orange Guarantee! (Sub text)
Vegan Formula (sub text)

The sub texts for above can be fun, have coloured background, different fonts, whatever looks good and is sill fun.

Towards the bottom of the front of bottle we require the sizing information:

200ml 6.7 Fl Oz

On the left side of the front (so in the template the middle smaller section) I would like the phrase "You ain't gotta get ready if you stay ready" Could you please make this as a separate little quote, with a fun design to it. It's like a little hidden gem on the side of the bottle.

On the back of the bottle for now can you please start towards the top with:

Amber Hush Mousse (larger)
Violet base (second heading)
Deep Mediterranean Inspired Tan (second heading)
Easy to Apply & Streak Free
Vegan friendly & 100% natural DHA tan actives

Under this I require approx 1.5" of Lorem Ipsum for now which will take the place of directions for using the product.

Under that in small writing can we include "Warning: This product does not contain a sunscreen and will not protect against sunburn. For external use only. If skin irritation occurs, discontinue use. Carry out a patch test 24 hours prior to full body use. Store below 25(degrees sign)C."

At the bottom is the smallest yet still legible writing, can we include the ingredients that are listed below.

Target Market(s)

Females 24-35 who take care of themselves and always want to look good. It's a youthful fun product.

Requirements
Must have
• Bright colours, and just screams FUN and youthful.

Ingredients must be listed on the back. They dont' need to take up more than an inch in height, less if possible.
*******************************************

INGREDIENTS: Water (Aqua), Propylene Glycol, Dihydroxyacetone, Peg-6 Caprylic/Capric Glycerides, Dihydroxypropyl Peg-5 Linoleammonium Chloride, Peg-7 Glyceryl Cocoate, Caramel,
Phenoxyethanol, Caprylyl Glycol, Potassium Sorbate, Hexylene Glycol, Glycerin, Helianthus Annuus (Sunflower) Seed Oil, Beta Vulgaris (Beet) Root Extract, Panthenol, Solanum Lycopersicum
(Tomato) Fruit Extract, Vaccinium Macrocarpon (Cranberry) Fruit Extract, L-ascorbic Acid (Vitamin C), Tocopheryl Acetate (Vitamin E), Theobroma Cacao (Cocoa) Seed Butter, Rosa Canina (Rose Hip)
Fruit Oil, Glycine Soja (Soybean) Oil, Cucumis Sativus (Cucumber) Fruit Extract, Blue 1 (CI 42090), Red 40 (CI 16035), Yellow 6 (CI 15985), Green 5 (CI 61570), Yellow 5 (CI 19140), Red 33 (CI 17200)

*****************************
Nice to have
• Several options to choose from, some can include a gradient into geometric shapes, rather than solid colour. Experiment
Should not have
• Do not want it to look medical.
Want colours to stay in the same pink family for the abstract design - can use white also.

```html
<!DOCTYPE html>
<html lang="en">
<head>
<meta charset="utf-8">
<title>Merrisol – Amber Hush Mousse Label</title>
<link href="https://fonts.googleapis.com/css2?family=Poppins:wght@400;500;600&family=Roboto:wght@400&display=swap" rel="stylesheet">
<style>
  :root{
    --backdrop:#e04d96;
    --white:#ffffff;
    --berry:#b0176f;
    --violet:#a01a78;
    --pink-1:#c2147a;
    --pink-2:#e8508f;
    --pink-3:#a3196e;
    --pink-4:#f06aa6;
    --pink-5:#d12d7f;
    --pink-6:#8e1266;
    --pink-7:#e91e7b;
    --pink-8:#c94a86;
    --ink:#222;
  }
  *{box-sizing:border-box;margin:0;padding:0}
  html,body{width:1200px;height:1200px;overflow:hidden}
  body{background:var(--backdrop);font-family:"Poppins",sans-serif;position:relative}

  .label{
    position:absolute;left:90px;top:270px;width:1020px;height:660px;
    display:flex;border-radius:6px;overflow:hidden;
  }
  .stripes{
    background:repeating-linear-gradient(90deg,
      var(--pink-1) 0 22px, var(--pink-4) 22px 34px, var(--pink-3) 34px 52px,
      var(--pink-7) 52px 70px, var(--pink-8) 70px 84px, var(--pink-6) 84px 100px,
      var(--pink-2) 100px 122px, var(--pink-5) 122px 136px, var(--pink-4) 136px 150px,
      var(--pink-1) 150px 172px, var(--pink-3) 172px 186px, var(--pink-7) 186px 208px,
      var(--pink-8) 208px 224px, var(--pink-6) 224px 240px);
  }
  .panel{position:relative;height:100%}
  .panel-back{width:420px}
  .panel-side{width:180px;background:var(--white)}
  .panel-front{width:420px}

  /* back */
  .back-arch{
    position:absolute;left:10px;right:10px;top:90px;bottom:0;
    background:var(--white);border-radius:200px 200px 0 0;
    padding:42px 26px 0;text-align:center;
  }
  .title-main{font-weight:600;font-size:38px;line-height:1.02;color:var(--berry)}
  .title-sub{font-weight:500;font-size:23px;color:var(--violet);margin-top:2px}
  .title-tan{font-weight:500;font-size:22px;line-height:1.2;color:var(--berry);margin-top:18px}
  .claims{list-style:none;text-align:left;margin:12px 0 0 26px}
  .claims li{display:flex;gap:6px;font-size:14px;line-height:1.15;color:var(--violet);margin-bottom:4px}
  .claims svg{flex:none;width:18px;height:18px}
  .info{text-align:left;margin-top:12px;font-family:"Roboto",sans-serif;font-size:8px;line-height:1.3;color:var(--ink)}
  .tag{display:inline-block;background:var(--pink-8);color:var(--white);font-family:"Poppins",sans-serif;font-size:10px;font-weight:500;padding:1px 8px;border-radius:10px;margin:8px 0 3px}
  .info p{text-align:justify}

  /* side */
  .side-stripes{position:absolute;left:0;right:0;top:0;height:560px;border-radius:0 0 90px 90px}
  .quote-pill{
    position:absolute;left:60px;top:60px;width:30px;height:400px;background:var(--white);
    border-radius:15px;display:flex;align-items:center;justify-content:center;
  }
  .quote-pill span{
    writing-mode:vertical-rl;font-size:12px;font-weight:500;letter-spacing:.5px;color:var(--pink-3);white-space:nowrap;
  }

  /* front */
  .brand-name{
    position:absolute;left:0;right:0;top:120px;text-align:center;
    font-weight:500;font-size:50px;letter-spacing:2px;color:var(--white);
  }
  .front-arch{
    position:absolute;left:10px;right:10px;top:380px;bottom:0;background:var(--white);
    border-radius:200px 200px 0 0;padding:60px 30px 0;text-align:center;
  }
  .front-title{font-weight:600;font-size:40px;line-height:1;color:var(--berry)}
  .front-sub{font-weight:500;font-size:23px;color:var(--violet);margin-top:4px}
  .pills{margin-top:20px;display:flex;flex-direction:column;align-items:center;gap:4px}
  .pill{color:var(--white);font-size:12px;padding:1px 0;border-radius:10px;width:210px}
  .pill-1{background:linear-gradient(90deg,var(--pink-8),var(--pink-4));margin-left:-30px}
  .pill-2{background:linear-gradient(90deg,var(--pink-4),var(--pink-1));margin-left:30px;width:220px}
  .pill-3{background:linear-gradient(90deg,var(--pink-7),var(--pink-3))}
  .size{margin-top:28px;font-size:14px;color:var(--berry)}
</style>
</head>
<body>
<div class="label stripes">
  <section class="panel panel-back">
    <div class="back-arch">
      <h1 class="title-main">Amber Hush<br>Mousse</h1>
      <h2 class="title-sub">Violet Base</h2>
      <h2 class="title-tan">Deep Mediterranean<br>Inspired Tan</h2>
      <ul class="claims">
        <li><svg viewBox="0 0 20 20"><circle cx="10" cy="10" r="8" fill="none" stroke="#a01a78" stroke-width="2"/><path d="M6 10l3 3 7-8" fill="none" stroke="#a01a78" stroke-width="2.4"/></svg>Easy to Apply &amp; Streak Free</li>
        <li><svg viewBox="0 0 20 20"><circle cx="10" cy="10" r="8" fill="none" stroke="#a01a78" stroke-width="2"/><path d="M6 10l3 3 7-8" fill="none" stroke="#a01a78" stroke-width="2.4"/></svg><span>Vegan friendly &amp; 100% natural<br>DHA tan actives</span></li>
      </ul>
      <div class="info">
        <span class="tag">USING:</span>
        <p>Lorem ipsum dolor sit amet, consectetuer adipiscing elit. Maecenas porttitor congue massa. Fusce posuere, magna sed pulvinar ultricies, purus lectus malesuada libero, sit amet commodo magna eros quis urna. Nunc viverra imperdiet enim. Fusce est. Vivamus a tellus. Pellentesque habitant morbi tristique senectus et netus et malesuada fames ac turpis egestas. Proin pharetra nonummy pede. Mauris et orci.</p>
        <span class="tag">WARNING:</span>
        <p>This product does not contain a sunscreen and will not protect against sunburn. For external use only. If skin irritation occurs, discontinue use. Carry out a patch test 24 hours prior to full body use. Store below 25°C.</p>
        <span class="tag">INGREDIENTS:</span>
        <p>Water (Aqua), Propylene Glycol, Dihydroxyacetone, Peg-6 Caprylic/Capric Glycerides, Dihydroxypropyl Peg-5 Linoleammonium Chloride, Peg-7 Glyceryl Cocoate, Caramel, Phenoxyethanol, Caprylyl Glycol, Potassium Sorbate, Hexylene Glycol, Glycerin, Helianthus Annuus (Sunflower) Seed Oil, Beta Vulgaris (Beet) Root Extract, Panthenol, Solanum Lycopersicum (Tomato) Fruit Extract, Vaccinium Macrocarpon (Cranberry) Fruit Extract, L-ascorbic Acid (Vitamin C), Tocopheryl Acetate (Vitamin E), Theobroma Cacao (Cocoa) Seed Butter, Rosa Canina (Rose Hip) Fruit Oil, Glycine Soja (Soybean) Oil, Cucumis Sativus (Cucumber) Fruit Extract, Blue 1 (CI 42090), Red 40 (CI 16035), Yellow 6 (CI 15985), Green 5 (CI 61570), Yellow 5 (CI 19140), Red 33 (CI 17200).</p>
      </div>
    </div>
  </section>

  <section class="panel panel-side">
    <div class="side-stripes stripes"></div>
    <div class="quote-pill"><span>YOU AIN'T GOTTA GET READY IF YOU STAY READY</span></div>
  </section>

  <section class="panel panel-front">
    <div class="brand-name">MERRISOL</div>
    <div class="front-arch">
      <h1 class="front-title">Amber Hush</h1>
      <h2 class="front-sub">Violet Base</h2>
      <div class="pills">
        <span class="pill pill-1">1 Hour Sunless Mousse</span>
        <span class="pill pill-2">The No Orange Guarantee!</span>
        <span class="pill pill-3">Vegan Formula</span>
      </div>
      <p class="size">200ml 6.7 Fl Oz</p>
    </div>
  </section>
</div>
</body>
</html>
```